A new presentation to our clients

we are a Real Estate agency, our website is www.lumibrasa.com and it’s time to have a new, fashion and remarcable Business Card. we want to differentiate ourselves from other companies so we want a business card that differentiates us. we want the business card to impact our customers. in the competitive market that we have today, we have to be different and it is this difference that we seek

Target Market(s)

Real Estate Clients

Contact Information for Business Card

We search a totaly diferent card from the usual

Font styles to use
Sans Serif

Colors
e34197

Requirements
Must have
• Logo, adress, phone contact, e-mail, photo, and our website
Nice to have
• We would like to see a modern business card
Should not have
• Houses or building draws

```html
<!DOCTYPE html>
<html lang="pt">
<head>
<meta charset="utf-8">
<title>Lumibrasa Business Card</title>
<link href="https://fonts.googleapis.com/css2?family=Roboto:wght@400;500;700&display=swap" rel="stylesheet">
<style>
  :root {
    --brand-pink: #e61e78;
    --brand-pink-light: #ec4a93;
    --paper-white: #ffffff;
    --backdrop: #3a3a3a;
  }
  * { margin: 0; padding: 0; box-sizing: border-box; }
  html, body { width: 1200px; height: 896px; overflow: hidden; }
  body {
    background: var(--backdrop);
    font-family: "Roboto", Arial, sans-serif;
    position: relative;
  }
  .card {
    position: absolute;
    top: 305px;
    width: 500px;
    height: 286px;
    border-radius: 18px;
    overflow: hidden;
  }
  .card-front {
    left: 70px;
    background: linear-gradient(135deg, var(--brand-pink-light) 0%, var(--brand-pink) 45%, var(--brand-pink) 100%);
    display: flex;
    align-items: center;
    justify-content: center;
  }
  .card-back { left: 630px; background: var(--paper-white); }
  .brand-name {
    font-family: "Roboto", Arial, sans-serif;
    font-weight: 500;
    letter-spacing: 1px;
  }
  .card-front .brand-name { color: var(--paper-white); font-size: 60px; }
  .card-back .brand-name {
    position: absolute;
    right: 30px;
    top: 24px;
    color: var(--brand-pink);
    font-size: 44px;
    line-height: 52px;
  }
  .back-shape { position: absolute; inset: 0; }
  .contact-block {
    position: absolute;
    left: 30px;
    top: 152px;
    color: var(--paper-white);
    font-size: 10.5px;
    line-height: 13px;
  }
  .person-name { font-size: 15px; font-weight: 700; line-height: 18px; text-transform: uppercase; }
  .person-role { margin-bottom: 5px; }
  .contact-line { display: flex; align-items: center; gap: 6px; }
  .contact-line svg { width: 8px; height: 8px; flex: none; }
  .address { margin-top: 5px; padding-left: 14px; }
</style>
</head>
<body>
  <section class="card card-front">
    <span class="brand-name">Lumibrasa</span>
  </section>

  <section class="card card-back">
    <svg class="back-shape" viewBox="0 0 500 286" preserveAspectRatio="none">
      <path d="M0,110 Q200,170 500,70 L500,286 L0,286 Z" fill="var(--brand-pink)"/>
      <path d="M0,99 Q200,159 500,59" fill="none" stroke="var(--brand-pink)" stroke-width="3"/>
    </svg>
    <span class="brand-name">Lumibrasa</span>
    <div class="contact-block">
      <div class="person-name">Daniel Moreira</div>
      <div class="person-role">Director</div>
      <div class="contact-line">
        <svg viewBox="0 0 10 10"><path d="M2,1 L4,1 L4.5,3.5 L3.2,4.3 Q4.5,6.5 5.7,6.8 L6.5,5.5 L9,6 L9,8 Q5,9.5 1,3 Z" fill="#fff"/></svg>
        <span>(+351) 220 555 140</span>
      </div>
      <div class="contact-line">
        <svg viewBox="0 0 10 10"><rect x="1" y="1" width="8" height="8" rx="1" fill="none" stroke="#fff"/></svg>
        <span>(+351) 220 555 148</span>
      </div>
      <div class="contact-line">
        <svg viewBox="0 0 10 10"><rect x="0.5" y="2" width="9" height="6" fill="none" stroke="#fff"/><path d="M0.5,2 L5,5.5 L9.5,2" fill="none" stroke="#fff"/></svg>
        <span>geral@lumibrasa.com</span>
      </div>
      <div class="contact-line">
        <svg viewBox="0 0 10 10"><circle cx="5" cy="5" r="4.2" fill="none" stroke="#fff"/><path d="M1,5 H9 M5,1 Q2.5,5 5,9 M5,1 Q7.5,5 5,9" fill="none" stroke="#fff" stroke-width="0.8"/></svg>
        <span>www.lumibrasa.com</span>
      </div>
      <div class="address">Rua das Acácias, 118<br>4400-512, Vila Clara</div>
    </div>
  </section>
</body>
</html>
```